Professional & attention grabbing.

A business card design, front and back. I already have a logo I will attach, but I am open to something new as well.
Things to include:
Name:
Title:
Phone:
Email:
Wanting something that is professional but attention grabbing.
Also we do a lot of work using drones on natural gas pipelines (leading the future)if you want to include any of that. I'm open to ideas.
Target Market(s)
Natural gas transmission industry / greenhouse gas mitigation industry
Industry/Entity Type
Business
Colors
Designer to choose colors to be used in the design.
Look and feel
Each slider illustrates characteristics of the customer's brand and the style your logo design should communicate.

```html
<!DOCTYPE html>
<html lang="en">
<head>
<meta charset="utf-8">
<title>Ridgeline Inspections – Business Card</title>
<link rel="stylesheet" href="https://fonts.googleapis.com/css2?family=Montserrat:wght@400;600;700&display=swap">
<style>
  :root {
    --red: #d12a35;
    --charcoal: #3b3b3e;
    --grey-text: #5d5d60;
    --paper: #ffffff;
    --backdrop: #e8e5e0;
    --card-w: 380px;
    --card-h: 660px;
  }
  * { box-sizing: border-box; margin: 0; padding: 0; }
  html, body {
    width: 1200px;
    height: 950px;
    overflow: hidden;
  }
  body {
    background: var(--backdrop);
    font-family: "Montserrat", Arial, sans-serif;
    display: flex;
    align-items: center;
    justify-content: center;
    gap: 90px;
  }
  .card {
    position: relative;
    width: var(--card-w);
    height: var(--card-h);
    background: var(--paper);
    border-radius: 24px;
    overflow: hidden;
    box-shadow: 0 6px 18px rgba(0,0,0,0.12);
  }

  /* Front */
  .card-front .top-band {
    position: absolute;
    top: 0; left: 0;
    width: 100%;
    height: 200px;
    display: block;
  }
  .card-front .brand-block {
    position: absolute;
    top: 220px;
    left: 44px;
    right: 44px;
    display: flex;
    align-items: center;
    gap: 16px;
  }
  .brand-square {
    flex: 0 0 auto;
    width: 22px;
    height: 22px;
    background: var(--red);
  }
  .brand-name {
    color: var(--charcoal);
    font-weight: 700;
    font-size: 34px;
    line-height: 1.1;
    letter-spacing: 0.5px;
  }
  .contact-block {
    position: absolute;
    left: 60px;
    bottom: 78px;
  }
  .person-name {
    color: var(--red);
    font-weight: 600;
    font-size: 26px;
    letter-spacing: 1.5px;
    text-transform: uppercase;
  }
  .person-title {
    color: var(--grey-text);
    font-size: 18px;
    margin: 6px 0 22px 4px;
  }
  .contact-list { list-style: none; }
  .contact-list li {
    display: flex;
    align-items: center;
    gap: 10px;
    color: var(--grey-text);
    font-size: 17px;
    margin-bottom: 10px;
  }
  .contact-list svg { width: 16px; height: 16px; flex: 0 0 auto; }

  /* Back */
  .card-back {
    display: flex;
    align-items: center;
    justify-content: center;
  }
  .card-back .brand-block {
    display: flex;
    align-items: center;
    gap: 18px;
  }
  .card-back .brand-name { font-size: 38px; }
</style>
</head>
<body>

  <article class="card card-front">
    <svg class="top-band" viewBox="0 0 380 200" preserveAspectRatio="none" aria-hidden="true">
      <path d="M0 0 H380 V120 C280 70 140 60 0 110 Z" fill="var(--red)"/>
    </svg>

    <div class="brand-block">
      <span class="brand-square"></span>
      <span class="brand-name">Ridgeline<br>Inspections</span>
    </div>

    <div class="contact-block">
      <h1 class="person-name">Daniel Reyes</h1>
      <p class="person-title">CEO/Founder</p>
      <ul class="contact-list">
        <li>
          <svg viewBox="0 0 16 16" aria-hidden="true"><path fill="var(--red)" d="M3.5 1.5l2.3 0 1.1 3.2-1.6 1.2c.8 1.8 2.1 3.1 3.9 3.9l1.2-1.6 3.2 1.1v2.3c0 1-.8 1.9-1.9 1.9C6.4 13.5 2.5 9.6 1.6 3.4c0-1 .9-1.9 1.9-1.9z"/></svg>
          <span>555 014 2290</span>
        </li>
        <li>
          <svg viewBox="0 0 16 16" aria-hidden="true"><rect x="1" y="3" width="14" height="10" rx="1.5" fill="var(--red)"/><path d="M1.8 4l6.2 4.6L14.2 4" stroke="#fff" stroke-width="1.3" fill="none"/></svg>
          <span>hello@ridgelineinspect.com</span>
        </li>
        <li>
          <svg viewBox="0 0 16 16" aria-hidden="true"><circle cx="8" cy="8" r="7" fill="var(--red)"/><path d="M1 8h14M8 1c-2.6 2.8-2.6 11.2 0 14M8 1c2.6 2.8 2.6 11.2 0 14" stroke="#fff" stroke-width="1" fill="none"/></svg>
          <span>www.ridgelineinspect.com</span>
        </li>
      </ul>
    </div>
  </article>

  <article class="card card-back">
    <div class="brand-block">
      <span class="brand-square"></span>
      <span class="brand-name">Ridgeline<br>Inspections</span>
    </div>
  </article>

</body>
</html>
```